Harbour Tote

I am developing a web site which sells preowned high end designer handbags and accessories. Some of the brands include: Varenne, Marcel Ostrand & Belmo, to name a few. I am after a luxurious and high end feel.

Some brands I like that express this feel include: Quintel, Belmo, fabcloset.com, pursepassonpaw.com

I am after a logo, business card, letterhead, with compliments, address label and envelope designs.
The business name is Lush satchel, and the website will be www.lushsatchel.com.au. I have thoughts of using LSC as a logo or LUSH satchel.com.au

I don't want a large logo, it needs to blend in with the name in some way - or may not need an image at all, if the style of the font speaks to the brand.

Thank-you
Updates

Project Deadline Extended
Reason: I would like to give designers plenty of time to be able to submit a design.

Target Market(s)

Women, aged 25-60 who are into fashion

Industry/Entity Type

Business

Requirements
Must have
• High End
Luxurious

```html
<!DOCTYPE html>
<html lang="en">
<head>
<meta charset="utf-8">
<title>Harbour Tote – Envelope Designs</title>
<link rel="stylesheet" href="https://fonts.googleapis.com/css2?family=Open+Sans:wght@600&display=swap">
<style>
  :root {
    --paper: #ffffff;
    --ink: #1a1a1a;
    --brand-red: #c12043;
    --line: #2a2a2a;
  }
  html, body {
    margin: 0;
    padding: 0;
    width: 1200px;
    height: 972px;
    overflow: hidden;
    background: var(--paper);
  }
  .canvas {
    position: relative;
    width: 1200px;
    height: 972px;
    font-family: "Open Sans", Arial, sans-serif;
    color: var(--ink);
  }
  .envelope {
    position: absolute;
    box-sizing: border-box;
    background: var(--paper);
    border: 3.5px solid var(--line);
    overflow: hidden;
  }
  .envelope--back {
    left: 10px;
    top: 0;
    width: 1184px;
    height: 428px;
    border-top: none;
  }
  .envelope--front {
    left: 4px;
    top: 544px;
    width: 1190px;
    height: 424px;
  }
  .flap {
    position: absolute;
    left: 0;
    top: 0;
    width: 100%;
    height: 250px;
  }
  .brand-name {
    position: absolute;
    margin: 0;
    font-weight: 600;
    line-height: 1;
    color: var(--ink);
    white-space: nowrap;
  }
  .envelope--back .brand-name {
    left: 26px;
    top: 190px;
    font-size: 46px;
    letter-spacing: 0.5px;
  }
  .web-address {
    position: absolute;
    margin: 0;
    font-weight: 600;
    line-height: 1;
    color: var(--ink);
    white-space: nowrap;
  }
  .envelope--back .web-address {
    left: 26px;
    top: 350px;
    font-size: 34px;
  }
  .brand-mark {
    position: absolute;
    left: 60px;
    top: 32px;
    width: 140px;
    height: 148px;
    background: var(--brand-red);
  }
  .envelope--front .web-address {
    left: 56px;
    top: 188px;
    font-size: 14px;
  }
  .address-window {
    position: absolute;
    left: 708px;
    top: 248px;
    width: 434px;
    height: 128px;
    box-sizing: border-box;
    border: 3.5px solid var(--line);
    border-radius: 64px;
  }
</style>
</head>
<body>
  <main class="canvas">
    <section class="envelope envelope--back" aria-label="Envelope back">
      <svg class="flap" viewBox="0 0 1184 250" preserveAspectRatio="none" aria-hidden="true">
        <polygon points="0,0 1184,0 602,240" fill="var(--brand-red)"/>
      </svg>
      <p class="brand-name">Harbour Tote</p>
      <p class="web-address">harbourtote.example</p>
    </section>

    <section class="envelope envelope--front" aria-label="Envelope front">
      <div class="brand-mark" aria-hidden="true"></div>
      <p class="web-address">harbourtote.example</p>
      <div class="address-window" aria-label="Address window"></div>
    </section>
  </main>
</body>
</html>
```